Black Car Limousine transportation business in Naples Florida

Steadfast stand for my reliability and RVD stands for Love, K and M are the first initials of my children's names. It should show professionalism and a dedication to customer service. We keep our clients identities private. Show our professionalism. We are Black car Black tie company. We service transportation on a reserve basis to and from residents, airports, casinos, hotels,

Target Market(s)

It is a Private car service. High end clients. Businesses, Celebrity and athletes. Service to airports, hotels, special events.

Industry/Entity Type

Business

Contact Information for Business Card

A pearl metallic or Luster card. Standard business card size. Would like the name, Company email, show we take credit cards and phone number. Currently I don't have a website but will like to add later.

Logo Text

STEADFAST RVD TRANSPORTATION

Font styles to use
Serif

Colors
eaeaea
000000

Requirements
Must have
• Must have Company email, show we take credit cards and phone number. Currently I don't have a website but will like to add later.
Nice to have
• Would like to stay with a black and white theme. Open to some color trim.
Should not have
• Open to suggestions

```html
<!DOCTYPE html>
<html lang="en">
<head>
<meta charset="utf-8">
<title>Steadfast RVD Transportation – Business Card</title>
<link rel="stylesheet" href="https://fonts.googleapis.com/css2?family=Lora:wght@400;600&display=swap">
<style>
  :root {
    --stage: #eaeaea;
    --ink: #000000;
    --paper: #ffffff;
    --band-grey: #4d4d4d;
    --soft-grey: #bdbdbd;
    --car-light: #5a5a5a;
    --car-dark: #111111;
  }
  * { box-sizing: border-box; margin: 0; padding: 0; }
  html, body {
    width: 1200px; height: 900px; overflow: hidden;
    background: var(--stage);
    font-family: "Lora", Georgia, serif;
  }
  .canvas {
    width: 1200px; height: 900px;
    display: flex; align-items: center; justify-content: center; gap: 40px;
  }
  .card {
    width: 540px; height: 309px; position: relative; overflow: hidden;
    box-shadow: 0 6px 18px rgba(0,0,0,.18);
  }

  /* Back side */
  .card-back { background: var(--ink); color: var(--paper); }
  .card-back .car-photo {
    position: absolute; left: 335px; top: 82px; width: 180px; height: 110px;
    border-radius: 14px 30px 10px 10px;
    background: radial-gradient(ellipse at 50% 40%, var(--car-light), var(--car-dark) 75%);
  }
  .card-back .wordmark { position: absolute; left: 70px; top: 88px; color: var(--paper); }

  /* Wordmark: one font, one weight, one colour */
  .wordmark { font-weight: 600; line-height: 1; }
  .wordmark .line-top { display: block; font-size: 18px; letter-spacing: 3px; margin-bottom: 4px; }
  .wordmark .line-main { display: block; font-size: 58px; letter-spacing: 4px; }
  .wordmark .line-sub { display: block; font-size: 19px; letter-spacing: 1.5px; margin-top: 4px; }

  /* Front side */
  .card-front { background: var(--paper); }
  .card-front .wordmark { position: absolute; left: 180px; top: 26px; color: var(--ink); }
  .contact-band {
    position: absolute; left: 0; top: 156px; width: 100%; height: 82px;
    background: var(--ink); color: var(--paper);
    display: flex; align-items: center; justify-content: center; gap: 14px;
    padding-left: 60px;
  }
  .person { text-align: right; }
  .person-name { font-size: 16px; font-weight: 600; }
  .person-role { font-size: 12px; }
  .divider { width: 1px; height: 40px; background: var(--soft-grey); }
  .contact-list { list-style: none; font-size: 12px; line-height: 1.6; }
  .contact-list li { display: flex; align-items: center; gap: 6px; }
  .contact-list svg { width: 11px; height: 11px; fill: var(--paper); }
  .address-band {
    position: absolute; left: 0; top: 238px; width: 100%; height: 71px;
    background: var(--band-grey); color: var(--paper);
    display: flex; flex-direction: column; align-items: center; justify-content: center; gap: 4px;
    font-size: 13px; letter-spacing: .3px;
  }
  .payment-note { display: flex; align-items: center; gap: 6px; font-size: 11px; color: var(--stage); }
  .payment-note svg { width: 16px; height: 11px; }
</style>
</head>
<body>
<main class="canvas">
  <section class="card card-back">
    <div class="car-photo" role="img" aria-label="Photograph of a black luxury SUV"></div>
    <div class="wordmark">
      <span class="line-top">STEADFAST</span>
      <span class="line-main">RVD</span>
      <span class="line-sub">TRANSPORTATION</span>
    </div>
  </section>

  <section class="card card-front">
    <div class="wordmark">
      <span class="line-top">STEADFAST</span>
      <span class="line-main">RVD</span>
      <span class="line-sub">TRANSPORTATION</span>
    </div>
    <div class="contact-band">
      <div class="person">
        <p class="person-name">Marcus Bell</p>
        <p class="person-role">Managing Director</p>
      </div>
      <span class="divider"></span>
      <ul class="contact-list">
        <li>
          <svg viewBox="0 0 24 24" aria-hidden="true"><path d="M6.6 10.8a15 15 0 0 0 6.6 6.6l2.2-2.2a1 1 0 0 1 1-.25 11.4 11.4 0 0 0 3.6.57 1 1 0 0 1 1 1V20a1 1 0 0 1-1 1A17 17 0 0 1 3 4a1 1 0 0 1 1-1h3.5a1 1 0 0 1 1 1c0 1.250.2 2.450.57 3.570a1 1 0 0 1-.25 1z"/></svg>
          (239) 555-0148
        </li>
        <li>
          <svg viewBox="0 0 24 24" aria-hidden="true"><path d="M2 5h20v14H2z M2 5l10 8 10-8" fill="none" stroke="#fff" stroke-width="2"/></svg>
          hello@rvdtransport.com
        </li>
      </ul>
    </div>
    <div class="address-band">
      <p>410 Harbor Lane, Naples, FL 34102</p>
      <p class="payment-note">
        <svg viewBox="0 0 16 11" aria-hidden="true"><rect x="0.5" y="0.5" width="15" height="10" rx="1.5" fill="none" stroke="#eaeaea"/><rect x="0.5" y="3" width="15" height="2" fill="#eaeaea"/></svg>
        All major credit cards accepted
      </p>
    </div>
  </section>
</main>
</body>
</html>
```